Exciting & Elegant Stationary Pack

Stationary consists of
1. Letter head / Envelope
2. Business Card
3. Invoice
4. 40x40mm sticker

Attached files;

1. Logo (Other formats available on request)
2. MS word Doc - For information and description of design
3. Website image (This will be our new website so use the colours so everything ties together)
4. Sample of stationary pack we like, but feel free to be creative

Target Market(s)

Home improvement

Industry/Entity Type

Construction

Font styles to use
Other font styles liked:
• Leave up to designer - We like font used on (website attached image)

Requirements
Must have
• Please look at uploaded file of sample website and use colours
Nice to have
• Any type of business card design - eg. metal, die cut, embossed, etc...

```html
<!DOCTYPE html>
<html lang="en">
<head>
<meta charset="utf-8">
<title>Setter by Craft — Stationery Cover</title>
<link rel="stylesheet" href="https://fonts.googleapis.com/css2?family=Josefin+Sans:wght@700&display=swap">
<style>
  :root {
    --navy-deep: #0a3a5e;
    --navy-light: #1f4f70;
    --signal-red: #c9262e;
    --sky-blue: #9ac2e2;
    --paper-white: #ffffff;
    --page-bg: #ffffff;
  }
  * { margin: 0; padding: 0; box-sizing: border-box; }
  html, body {
    width: 1200px;
    height: 873px;
    overflow: hidden;
    background: var(--page-bg);
  }
  .cover {
    position: relative;
    width: 1200px;
    height: 873px;
    overflow: hidden;
  }
  .cover__field {
    position: absolute;
    left: 0; top: 0;
    width: 1200px;
    height: 711px;
    background:
      linear-gradient(118deg,
        var(--navy-deep) 0%,
        var(--navy-light) 22%,
        var(--navy-light) 38%,
        var(--navy-deep) 62%,
        var(--navy-deep) 100%);
  }
  .cover__band--red {
    position: absolute;
    left: 0; top: 711px;
    width: 1200px;
    height: 80px;
    background: var(--signal-red);
  }
  .cover__band--sky {
    position: absolute;
    left: 0; top: 791px;
    width: 1200px;
    height: 82px;
    background: var(--sky-blue);
  }
  .brand {
    position: absolute;
    left: 786px;
    top: 580px;
    font-family: "Josefin Sans", sans-serif;
    font-weight: 700;
    color: var(--paper-white);
    line-height: 1;
  }
  .brand__name {
    display: block;
    font-size: 64px;
    letter-spacing: 1px;
  }
  .brand__tagline {
    display: block;
    margin-top: 14px;
    padding-left: 80px;
    font-size: 28px;
    letter-spacing: 0.5px;
  }
</style>
</head>
<body>
  <main class="cover">
    <div class="cover__field"></div>
    <div class="cover__band--red"></div>
    <div class="cover__band--sky"></div>
    <div class="brand">
      <span class="brand__name">SETTER</span>
      <span class="brand__tagline">by CRAFT</span>
    </div>
  </main>
</body>
</html>
```